VENTURE CAPITAL GROUP BUSINESS CARD DESIGN

Venture Capital Group based in SF looking for a bold business card design. No trendy colour explosion, 3D effects etc. Just "simple" optical effects. Works on your brain, keeps your eye focused and sticks to your mind.
Target Market(s)
Technology startups
Industry/Entity Type
Venture Capital
Contact Information for Business Card
DESMOND WHITLAKE
MANAGING PARTNER
187 FENWORTH ST SAN FRANCISCO, CA 94187
415.555.0142 O
415.555.0147 F
415.555.0193 C
desmond@veldtmoorcapital.ventures

```html
<!DOCTYPE html>
<html lang="en">
<head>
<meta charset="utf-8">
<title>Veldtmoor Capital Group — Business Card</title>
<link rel="stylesheet" href="https://fonts.googleapis.com/css2?family=Open+Sans:wght@400;600;700&display=swap">
<style>
  :root {
    --backdrop: #262626;
    --card-black: #050505;
    --brand-green: #3fb84a;
    --deep-green: #1f7a2e;
    --silver: #b9bbbd;
    --white: #ffffff;
    --mark-white: #f2f2f2;
  }
  * { margin: 0; padding: 0; box-sizing: border-box; }
  html, body {
    width: 1200px; height: 900px; overflow: hidden;
    background: var(--backdrop);
    font-family: "Open Sans", Arial, sans-serif;
  }
  .canvas { position: relative; width: 1200px; height: 900px; }
  .card {
    position: absolute; width: 640px; height: 365px;
    border-radius: 22px; overflow: hidden;
    background: var(--card-black);
    box-shadow: 0 18px 40px rgba(0,0,0,.55);
  }
  .card-front { left: 90px; top: 70px; }
  .card-back { left: 470px; top: 465px; }

  .front-brand {
    position: absolute; left: 0; right: 0; top: 88px;
    display: flex; flex-direction: column; align-items: center;
  }
  .brand-disc {
    width: 112px; height: 112px; border-radius: 50%;
    background: var(--mark-white);
  }
  .brand-name {
    color: var(--deep-green); font-weight: 600;
    letter-spacing: 3px; text-transform: uppercase; line-height: 1.15;
  }
  .front-brand .brand-name { margin-top: 22px; font-size: 30px; text-align: center; }
  .front-brand .brand-name span { display: block; font-size: 13px; letter-spacing: 5px; }

  .back-swoosh { position: absolute; inset: 0; }
  .back-disc {
    position: absolute; right: 40px; top: 22px;
    width: 118px; height: 118px; border-radius: 50%;
    background: var(--mark-white); border: 3px solid var(--silver);
  }
  .back-brand { position: absolute; left: 40px; top: 140px; }
  .back-brand .brand-name { font-size: 28px; }
  .back-brand .brand-name span { display: block; font-size: 12px; letter-spacing: 5px; }

  .person { position: absolute; left: 40px; top: 222px; color: var(--white); }
  .person-name { font-size: 22px; font-weight: 700; letter-spacing: 1px; }
  .person-title { font-size: 13px; font-weight: 700; color: var(--brand-green); letter-spacing: 1px; }
  .person-address { margin-top: 14px; font-size: 13px; font-weight: 600; line-height: 1.35; letter-spacing: .5px; }

  .contacts {
    position: absolute; right: 28px; top: 168px;
    list-style: none; color: var(--white);
    font-size: 13px; font-weight: 600; text-align: right; line-height: 1.45;
  }
  .contacts li { display: flex; justify-content: flex-end; align-items: center; gap: 8px; }
  .contacts svg { width: 11px; height: 11px; fill: none; stroke: var(--white); stroke-width: 1.6; }
  .email { position: absolute; right: 28px; bottom: 40px; color: var(--white); font-size: 14px; font-weight: 600; }
</style>
</head>
<body>
<main class="canvas">

  <section class="card card-front" aria-label="Card front">
    <div class="front-brand">
      <div class="brand-disc"></div>
      <p class="brand-name">Veldtmoor<span>Capital Group</span></p>
    </div>
  </section>

  <section class="card card-back" aria-label="Card back">
    <svg class="back-swoosh" viewBox="0 0 640 365" preserveAspectRatio="none" aria-hidden="true">
      <path fill="var(--brand-green)" d="M640 0 L440 0 C390 60 400 200 300 290 C230 350 100 330 -20 318 L-20 365 L640 365 Z"/>
      <path fill="var(--card-black)" d="M640 0 L448 0 C398 60 408 203 308 293 C238 352 108 336 -20 326 L-20 365 L640 365 Z"/>
      <path fill="var(--silver)" d="M640 0 L458 0 C408 62 420 207 318 297 C248 356 118 342 -20 334 L-20 365 L640 365 Z"/>
      <path fill="var(--brand-green)" d="M640 0 L474 0 C424 66 440 212 336 302 C266 362 140 352 -20 346 L-20 365 L640 365 Z"/>
    </svg>

    <div class="back-disc"></div>

    <div class="back-brand">
      <p class="brand-name">Veldtmoor<span>Capital Group</span></p>
    </div>

    <div class="person">
      <p class="person-name">DESMOND WHITLAKE</p>
      <p class="person-title">MANAGING PARTNER</p>
      <p class="person-address">187 FENWORTH ST SAN<br>FRANCISCO, CA 94187</p>
    </div>

    <ul class="contacts">
      <li>415.555.0142
        <svg viewBox="0 0 12 12"><path d="M2 1 L4.5 1 L5.5 4 L4 5 C5 7 6 8 7 8.5 L8 7 L11 8 L11 10.5 C6 11 1 6 2 1 Z"/></svg></li>
      <li>415.555.0147
        <svg viewBox="0 0 12 12"><rect x="1" y="5" width="10" height="5"/><rect x="3" y="1.5" width="6" height="3.5"/></svg></li>
      <li>415.555.0193
        <svg viewBox="0 0 12 12"><rect x="3" y="1" width="6" height="10" rx="1"/></svg></li>
      <li>&nbsp;
        <svg viewBox="0 0 12 12"><rect x="1" y="2.5" width="10" height="7"/><path d="M1 2.5 L6 7 L11 2.5"/></svg></li>
    </ul>
    <p class="email">desmond@veldtmoorcapital.ventures</p>
  </section>

</main>
</body>
</html>
```